Redesign Website - Current one too plain

The description is in the uploaded file. Please let me know if you need any more information. I'd prefer it if someone could implement the design to a WordPress site but the best design will win, regardless.
I would like the forms to look nice as well
UPDATE:
I don't think we can use the images that I provided, I think they make the site look a bit 'cheap' and I really don't know how to replace them. One thought I have had is to make the "Simple, Unique, Effective" a second feature on the right side of the page with the search on the left
Target Market(s)
Small companies, private sellers of cars and people who rent their caravan/holiday home out
Industry/Entity Type
Advertising
Number of Pages Required
3 page
Colors
Designer to choose colors to be used in the design.
Look and feel
Each slider illustrates characteristics of the customer's brand and the style your logo design should communicate.

```html
<!DOCTYPE html>
<html lang="en">
<head>
<meta charset="utf-8">
<title>KODRA – Find advertisers by code</title>
<link rel="stylesheet" href="https://fonts.googleapis.com/css2?family=Nunito:wght@300;400;600;700;800&family=Lato:wght@400&display=swap">
<style>
:root{
  --yellow:#fff200;
  --ink:#111111;
  --text:#3a3a3a;
  --muted:#555555;
  --light:#f3f3f4;
  --white:#ffffff;
  --dark:#1e1e1e;
  --line:#3a3a3a;
}
*{margin:0;padding:0;box-sizing:border-box}
html,body{width:1200px;height:3174px;overflow:hidden}
body{position:relative;font-family:'Nunito',sans-serif;color:var(--text);background:var(--white)}
.abs{position:absolute}
.brand{display:flex;align-items:center;gap:10px;font-weight:700;font-size:27px;color:var(--ink);letter-spacing:.5px}
.brand-dot{width:34px;height:34px;border-radius:50%;background:var(--yellow)}
.site-header{left:0;top:0;width:1200px;height:89px;background:var(--white)}
.nav a{position:absolute;top:34px;font-size:15px;color:var(--ink);text-decoration:none;letter-spacing:.3px}
.nav .active::after{content:"";position:absolute;left:-2px;right:-2px;bottom:-7px;height:2px;background:var(--yellow)}
.pill{position:absolute;display:flex;align-items:center;justify-content:center;border-radius:20px;font-size:15px;color:var(--ink);background:var(--yellow)}
.hero{left:0;top:89px;width:1200px;height:641px;background:var(--light)}
.code-letter{position:absolute;font-weight:300;font-size:112px;line-height:1;color:var(--ink);text-align:center;width:100px}
.chev{position:absolute;width:38px;height:38px;border-radius:50%;background:var(--white);display:flex;align-items:center;justify-content:center}
.filter{position:absolute;top:328px;height:35px;border:1.5px solid #333;border-radius:18px;font-size:12px;display:flex;align-items:center;justify-content:center;color:var(--ink);background:var(--white)}
.filter.search{border:none;background:var(--yellow)}
.photo{position:absolute}
.welcome{left:0;top:730px;width:1200px;height:650px;background:radial-gradient(ellipse 420px 520px at 0 300px,rgba(255,242,0,.22),rgba(255,255,255,0) 70%),radial-gradient(ellipse 320px 400px at 1200px 420px,rgba(255,242,0,.12),rgba(255,255,255,0) 70%),var(--white)}
.section-title{position:absolute;left:0;width:1200px;text-align:center;font-weight:800;font-size:27px;color:var(--ink);letter-spacing:.3px}
.rule{position:absolute;left:574px;width:52px;height:4px;background:var(--yellow)}
.intro{position:absolute;left:182px;top:884px;width:837px;text-align:center;font-size:17.5px;line-height:26px;font-weight:400;color:var(--text)}
.card{position:absolute;top:1075px;width:291px;height:243px;background:var(--white);border-radius:10px;box-shadow:0 4px 22px rgba(0,0,0,.06);text-align:center}
.card svg{margin-top:44px}
.card h3{margin-top:18px;font-size:16px;font-weight:700;color:var(--ink)}
.card p{margin-top:14px;font-size:14px;line-height:21px;color:var(--muted);font-weight:400}
.features{left:0;top:1380px;width:1200px;height:647px;background:var(--light)}
.feature{position:absolute;width:320px;height:100px}
.feature .ico{position:absolute;left:0;top:0;width:66px;height:70px;background:var(--white);border-radius:10px;display:flex;align-items:center;justify-content:center}
.feature h4{position:absolute;left:87px;top:0;font-size:16px;font-weight:700;color:var(--ink)}
.feature p{position:absolute;left:87px;top:25px;width:200px;font-size:11px;line-height:13.5px;color:var(--muted)}
.service{position:absolute;top:2175px;width:299px;text-align:center}
.service .photo{position:relative;width:299px;height:198px}
.service h3{margin-top:22px;font-size:16px;font-weight:700;color:var(--ink)}
.service p{margin-top:12px;font-size:14.5px;line-height:21px;color:var(--muted);padding:0 14px}
.testimonials{left:0;top:2526px;width:1200px;height:459px;background:var(--light)}
.quote{position:absolute;top:2661px;width:226px;height:274px;background:var(--white);text-align:center}
.quote .mark{margin-top:18px;font-size:56px;font-weight:800;line-height:56px;height:44px;color:var(--yellow);font-family:Georgia,serif}
.quote p{margin-top:10px;font-size:13px;line-height:17.8px;color:var(--text);padding:0 20px}
.quote .who{margin-top:14px;font-size:11.5px;font-weight:600;color:var(--ink)}
.footer{left:0;top:2985px;width:1200px;height:189px;background:var(--dark)}
.footer .brand{color:var(--white)}
.footer-nav a{position:absolute;top:3033px;font-size:15px;color:var(--white);text-decoration:none}
.copyright{position:absolute;left:0;top:3134px;width:1200px;text-align:center;font-family:'Lato',sans-serif;font-size:11px;color:var(--white)}
</style>
</head>
<body>

<header class="abs site-header">
  <div class="abs brand" style="left:133px;top:24px"><span class="brand-dot"></span>KODRA</div>
  <nav class="nav">
    <a class="active" style="left:572px">HOME</a>
    <a style="left:653px">ADVERTISE</a>
    <a style="left:775px">CONTACT</a>
  </nav>
  <div class="pill" style="left:874px;top:25px;width:103px;height:34px">REGISTER</div>
  <div class="pill" style="left:989px;top:25px;width:77px;height:34px">LOGIN</div>
</header>

<section class="abs hero">
  <div class="chev" style="left:536px;top:28px"><svg width="16" height="10" viewBox="0 0 16 10"><path d="M1 9L8 2l7 7" fill="none" stroke="#111" stroke-width="1.6"/></svg></div>
  <div class="chev" style="left:646px;top:28px"><svg width="16" height="10" viewBox="0 0 16 10"><path d="M1 9L8 2l7 7" fill="none" stroke="#111" stroke-width="1.6"/></svg></div>
  <div class="code-letter" style="left:507px;top:70px">A</div>
  <div class="code-letter" style="left:620px;top:70px">1</div>
  <div class="chev" style="left:536px;top:178px"><svg width="16" height="10" viewBox="0 0 16 10"><path d="M1 1l7 7 7-7" fill="none" stroke="#111" stroke-width="1.6"/></svg></div>
  <div class="chev" style="left:646px;top:178px"><svg width="16" height="10" viewBox="0 0 16 10"><path d="M1 1l7 7 7-7" fill="none" stroke="#111" stroke-width="1.6"/></svg></div>
</section>

<div class="filter" style="left:397px;width:79px">CAR</div>
<div class="filter" style="left:491px;width:106px">CARAVAN</div>
<div class="filter" style="left:611px;width:110px">COMPANY</div>
<div class="filter search" style="left:736px;width:111px">SEARCH</div>
<div class="pill" style="left:494px;top:392px;width:238px;height:39px">ADVERTISE YOUR COMPANY</div>

<div class="photo" role="img" aria-label="Dark grey SUV with a yellow X3 code sticker" style="left:12px;top:495px;width:400px;height:238px;background:radial-gradient(ellipse 190px 110px at 50% 55%,#4a4d52,#2b2d30 60%,rgba(243,243,244,0) 100%)"></div>
<div class="photo" role="img" aria-label="White panel van with a yellow F7 code sticker" style="left:426px;top:474px;width:356px;height:258px;background:radial-gradient(ellipse 170px 125px at 50% 50%,#ffffff,#dcdcdc 60%,rgba(243,243,244,0) 100%)"></div>
<div class="photo" role="img" aria-label="White house with orange tiled roof and a yellow A8 code sticker" style="left:807px;top:468px;width:393px;height:272px;background:linear-gradient(180deg,rgba(243,243,244,0) 0%,#d2643a 12%,#c85a30 32%,#eeeeee 38%,#e4e4e4 85%,rgba(243,243,244,0) 100%)"></div>

<section class="abs welcome"></section>
<h2 class="section-title" style="top:798px">WELCOME TO KODRA</h2>
<div class="rule" style="top:853px"></div>
<p class="intro">Lorem ipsum dolor sit amet, consectetur adipiscing elit sed do eiusmod tempor incididunt ut labore et dolore magna aliqua. Ut enim ad minim veniam quis nostrud exercitation ullamco laboris nisi ut aliquip ex ea commodo consequat. Duis aute irure dolor in reprehenderit in voluptate velit esse cillum.</p>
<div class="pill" style="left:539px;top:988px;width:123px;height:39px">READ MORE</div>

<article class="card" style="left:132px">
  <svg width="46" height="52" viewBox="0 0 46 52" fill="none" stroke="#111" stroke-width="1.8"><rect x="4" y="6" width="36" height="42" rx="2"/><path d="M14 3v6M30 3v6M11 18h8l6-4v12l-6-4h-8zM11 32h22M11 38h22M11 44h14"/></svg>
  <h3>SIMPLE</h3>
  <p>Create&nbsp; your advert and<br>display your code</p>
</article>
<article class="card" style="left:455px">
  <svg width="40" height="50" viewBox="0 0 40 50" fill="none" stroke="#111" stroke-width="1.8"><path d="M3 3h24l10 10v34H3z M27 3v10h10"/><circle cx="19" cy="29" r="7"/><path d="M24 34l7 7"/></svg>
  <h3>UNIQUE</h3>
  <p>customers find you by an<br>easy-to-remember code</p>
</article>
<article class="card" style="left:777px">
  <svg width="50" height="50" viewBox="0 0 50 50" fill="none" stroke="#111" stroke-width="1.8"><rect x="3" y="5" width="14" height="16"/><path d="M6 10h8M6 15h8"/><path d="M28 20l14-14 4 4-14 14z"/><circle cx="14" cy="34" r="6"/><rect x="28" y="30" width="16" height="14"/><path d="M3 46h44"/></svg>
  <h3>EFFECTIVE</h3>
  <p>customers are directed to you and<br>not a list of your competitors</p>
</article>

<section class="abs features"></section>
<h2 class="section-title" style="top:1432px">FEATURES</h2>
<div class="rule" style="top:1486px"></div>

<div class="feature" style="left:132px;top:1546px"><div class="ico"><svg width="30" height="30" viewBox="0 0 30 30" fill="none" stroke="#111" stroke-width="1.6"><circle cx="15" cy="15" r="12"/><path d="M9 15l4 4 8-9"/></svg></div><h4>Lorem ipsum dolor sit</h4><p>Sed ut perspiciatis unde omnis iste natus error sit voluptatem acc usant ium doloremque laudantium, totam rem operiam, eaque ipsa quae ab illo inventore veritatis</p></div>
<div class="feature" style="left:453px;top:1546px"><div class="ico"><svg width="30" height="34" viewBox="0 0 30 34" fill="none" stroke="#111" stroke-width="1.6"><circle cx="15" cy="13" r="9"/><path d="M11 22v5h8v-5M12 31h6"/><circle cx="15" cy="13" r="3"/></svg></div><h4>Lorem ipsum dolor sit</h4><p>Sed ut perspiciatis unde omnis iste natus error sit voluptatem acc usant ium doloremque laudantium, totam rem operiam, eaque ipsa quae ab illo inventore veritatis</p></div>
<div class="feature" style="left:780px;top:1546px"><div class="ico"><svg width="32" height="32" viewBox="0 0 32 32" fill="none" stroke="#111" stroke-width="1.6"><circle cx="16" cy="17" r="11"/><circle cx="16" cy="17" r="6"/><path d="M16 14v3l2 2M12 3h8"/></svg></div><h4>Lorem ipsum dolor sit</h4><p>Sed ut perspiciatis unde omnis iste natus error sit voluptatem acc usant ium doloremque laudantium, totam rem operiam, eaque ipsa quae ab illo inventore veritatis</p></div>

<div class="feature" style="left:132px;top:1704px"><div class="ico"><svg width="32" height="32" viewBox="0 0 32 32" fill="none" stroke="#111" stroke-width="1.6"><circle cx="16" cy="17" r="11"/><circle cx="16" cy="17" r="6"/><path d="M16 14v3l2 2M12 3h8"/></svg></div><h4>Lorem ipsum dolor sit</h4><p>Sed ut perspiciatis unde omnis iste natus error sit voluptatem acc usant ium doloremque laudantium, totam rem operiam, eaque ipsa quae ab illo inventore veritatis</p></div>
<div class="feature" style="left:453px;top:1704px"><div class="ico"><svg width="32" height="32" viewBox="0 0 32 32" fill="none" stroke="#111" stroke-width="1.6"><circle cx="16" cy="17" r="11"/><circle cx="16" cy="17" r="6"/><path d="M16 14v3l2 2M12 3h8"/></svg></div><h4>Lorem ipsum dolor sit</h4><p>Sed ut perspiciatis unde omnis iste natus error sit voluptatem acc usant ium doloremque laudantium, totam rem operiam, eaque ipsa quae ab illo inventore veritatis</p></div>
<div class="feature" style="left:780px;top:1704px"><div class="ico"><svg width="34" height="32" viewBox="0 0 34 32" fill="none" stroke="#111" stroke-width="1.6"><circle cx="17" cy="8" r="5"/><circle cx="10" cy="20" r="5"/><circle cx="24" cy="20" r="5"/><path d="M3 30h28"/></svg></div><h4>Lorem ipsum dolor sit</h4><p>Sed ut perspiciatis unde omnis iste natus error sit voluptatem acc usant ium doloremque laudantium, totam rem operiam, eaque ipsa quae ab illo inventore veritatis</p></div>

<div class="feature" style="left:132px;top:1869px"><div class="ico"><svg width="34" height="32" viewBox="0 0 34 32" fill="none" stroke="#111" stroke-width="1.6"><path d="M7 30V12M3 16l4-5 4 5M17 30V5M13 9l4-5 4 5M27 30V14M23 18l4-5 4 5"/></svg></div><h4>Lorem ipsum dolor sit</h4><p>Sed ut perspiciatis unde omnis iste natus error sit voluptatem acc usant ium doloremque laudantium, totam rem operiam, eaque ipsa quae ab illo inventore veritatis</p></div>
<div class="feature" style="left:453px;top:1869px"><div class="ico"><svg width="32" height="32" viewBox="0 0 32 32" fill="none" stroke="#111" stroke-width="1.6"><circle cx="15" cy="17" r="11"/><circle cx="15" cy="17" r="6"/><circle cx="15" cy="17" r="1.5"/><path d="M15 17L28 4M24 4h4v4"/></svg></div><h4>Lorem ipsum dolor sit</h4><p>Sed ut perspiciatis unde omnis iste natus error sit voluptatem acc usant ium doloremque laudantium, totam rem operiam, eaque ipsa quae ab illo inventore veritatis</p></div>
<div class="feature" style="left:780px;top:1869px"><div class="ico"><svg width="34" height="34" viewBox="0 0 34 34" fill="none" stroke="#111" stroke-width="1.6"><circle cx="17" cy="17" r="14"/><circle cx="17" cy="17" r="10"/><path d="M11 20l4-4 3 3 5-6"/></svg></div><h4>Lorem ipsum dolor sit</h4><p>Sed ut perspiciatis unde omnis iste natus error sit voluptatem acc usant ium doloremque laudantium, totam rem operiam, eaque ipsa quae ab illo inventore veritatis</p></div>

<h2 class="section-title" style="top:2074px">OUR SERVICES</h2>
<div class="rule" style="top:2128px"></div>

<article class="service" style="left:131px">
  <div class="photo" role="img" aria-label="White box van parked by an orange building, yellow F7 code sticker" style="background:linear-gradient(90deg,#9ea6ae 0%,#e9ecef 30%,#f2f2f2 55%,#e07a2a 75%,#c9652a 100%)"></div>
  <h3>VAN</h3>
  <p>Sed ut perspiciatis unde omnis iste natus error sit voluptatem accusantium</p>
</article>
<article class="service" style="left:448px">
  <div class="photo" role="img" aria-label="Dark blue SUV at sunset, yellow X3 code sticker" style="background:linear-gradient(180deg,#f0b56a 0%,#c98a58 30%,#1d2a5c 60%,#141a33 100%)"></div>
  <h3>CAR</h3>
  <p>Sed ut perspiciatis unde omnis iste natus error sit voluptatem accusantium</p>
</article>
<article class="service" style="left:766px">
  <div class="photo" role="img" aria-label="White caravan parked on open grassland, yellow A8 code sticker" style="background:linear-gradient(180deg,#9e8f78 0%,#b9ab90 40%,#e8e6e0 55%,#a8997d 100%)"></div>
  <h3>CARAVAN</h3>
  <p>Sed ut perspiciatis unde omnis iste natus error sit voluptatem accusantium</p>
</article>

<section class="abs testimonials"></section>
<h2 class="section-title" style="top:2568px">TESTIMONIALS</h2>
<div class="rule" style="top:2622px"></div>
<svg class="abs" style="left:87px;top:2789px" width="14" height="22" viewBox="0 0 14 22"><path d="M12 1L2 11l10 10" fill="none" stroke="#111" stroke-width="1.8"/></svg>
<svg class="abs" style="left:1098px;top:2789px" width="14" height="22" viewBox="0 0 14 22"><path d="M2 1l10 10L2 21" fill="none" stroke="#111" stroke-width="1.8"/></svg>

<blockquote class="quote" style="left:133px"><div class="mark">“</div><p>Sed ut perspiciatis unde omnis iste natus error sit volu ptatem acc usant ium dolo remque laudantium, totam rem ape riam, eaque ipsa quae ab illo inventore veritatis Nemo enim ipsam voluptatem quia volup tas sit.</p><div class="who">MARTIN</div></blockquote>
<blockquote class="quote" style="left:370px"><div class="mark">“</div><p>Sed ut perspiciatis unde omnis iste natus error sit volu ptatem acc usant ium dolo remque laudantium, totam rem ape riam, eaque ipsa quae ab illo inventore veritatis Nemo enim ipsam voluptatem quia volup tas sit.</p><div class="who">MARTIN</div></blockquote>
<blockquote class="quote" style="left:607px"><div class="mark">“</div><p>Sed ut perspiciatis unde omnis iste natus error sit volu ptatem acc usant ium dolo remque laudantium, totam rem ape riam, eaque ipsa quae ab illo inventore veritatis Nemo enim ipsam voluptatem quia volup tas sit.</p><div class="who">MARTIN</div></blockquote>
<blockquote class="quote" style="left:844px"><div class="mark">“</div><p>Sed ut perspiciatis unde omnis iste natus error sit volu ptatem acc usant ium dolo remque laudantium, totam rem ape riam, eaque ipsa quae ab illo inventore veritatis Nemo enim ipsam voluptatem quia volup tas sit.</p><div class="who">MARTIN</div></blockquote>

<footer class="abs footer">
  <div class="abs brand" style="left:133px;top:45px"><span class="brand-dot"></span>KODRA</div>
  <div class="abs" style="left:132px;top:116px;width:935px;height:1px;background:var(--line)"></div>
</footer>
<nav class="footer-nav">
  <a style="left:612px">HOME</a>
  <a style="left:693px">ADVERTISE</a>
  <a style="left:815px">CONTACT</a>
  <a style="left:922px">LOGIN</a>
  <a style="left:1008px">SEARCH</a>
</nav>
<p class="copyright">Copyright © 2023 All Rights Reserved</p>

</body>
</html>
```